Mobile friendly Website design

Client is a packaging equipment company that would like a clean, mobile friendly design. They want a different home page than what they have now. The home page should have the traditional sliders, content area, services are and a featured products area. Please provide an internal page design too.

Target Market(s)

Companies who use packaging equipment, shrink wrappers, heat sealers and carton erectors.

Industry/Entity Type

It Company

Number of Pages Required

2 page

Font styles to use
Serif
Sans Serif

Requirements
Must have
• Must have a clean, mobile friendly design.

```html
<!DOCTYPE html>
<html lang="en">
<head>
<meta charset="utf-8">
<title>Northgate Companies – Packaging Equipment</title>
<link href="https://fonts.googleapis.com/css2?family=Montserrat:wght@400;500;600;700&family=Open+Sans:wght@400;600&display=swap" rel="stylesheet">
<style>
:root{
  --red:#a61e2f;
  --navy:#2b2562;
  --navy-dark:#201b50;
  --ink:#222;
  --muted:#666;
  --light:#999;
  --band:#e3e3e3;
  --line:#d4d4d4;
  --white:#fff;
}
*{box-sizing:border-box;margin:0;padding:0}
html,body{width:1200px;height:2462px;overflow:hidden}
body{position:relative;background:var(--white);font-family:"Open Sans",Arial,sans-serif;color:var(--ink)}
h1,h2,h3,h4,h5{font-weight:400}
.abs{position:absolute}
a{color:inherit;text-decoration:none}

/* header */
.site-header{left:0;top:0;width:1200px;height:100px}
.brand{left:145px;top:24px;display:flex;align-items:center;gap:10px;font-family:"Montserrat",Arial,sans-serif;font-weight:700;font-size:22px;line-height:24px;color:var(--red)}
.brand-mark{width:14px;height:14px;background:var(--red);flex:none}
.main-nav{left:411px;top:44px;display:flex;gap:21px;font-family:"Montserrat",Arial,sans-serif;font-size:14px;color:#333}

/* hero */
.hero{left:0;top:100px;width:1200px;height:481px;background:linear-gradient(180deg,#b9b8bd 0%,#a7a4a6 45%,#7d7566 70%,#c9c6c6 100%)}
.hero-rule{left:0;top:581px;width:1200px;height:5px;background:linear-gradient(90deg,var(--navy),var(--red))}
.hero-title{left:0;top:274px;width:1200px;text-align:center;font-family:"Montserrat",Arial,sans-serif;font-size:36px;font-weight:500;color:var(--white);letter-spacing:.5px}
.hero-sub{left:0;top:322px;width:1200px;text-align:center;font-family:"Montserrat",Arial,sans-serif;font-size:30px;font-weight:500;color:var(--white)}
.hero-btn{left:519px;top:384px;width:162px;height:40px;border:2px solid var(--white);color:var(--white);font-family:"Montserrat",Arial,sans-serif;font-size:16px;display:flex;align-items:center;justify-content:center}
.slider-dots{left:555px;top:544px;display:flex;gap:4px}
.slider-dots span{width:18px;height:18px;border-radius:50%;background:var(--white)}
.slider-dots span.is-active{background:transparent;border:2px solid var(--white)}

/* intro */
.intro-title{left:0;top:636px;width:1200px;text-align:center;font-family:"Montserrat",Arial,sans-serif;font-weight:400;font-size:30px;line-height:38px;color:var(--ink)}
.intro-text{left:164px;top:724px;width:868px;text-align:center;font-size:13px;line-height:24px;color:var(--muted)}
.btn-dark{left:539px;top:818px;width:128px;height:39px;background:var(--navy-dark);color:var(--white);border-radius:3px;font-family:"Montserrat",Arial,sans-serif;font-weight:600;font-size:13px;display:flex;align-items:center;justify-content:center}

/* service cards */
.service{top:913px;width:285px;height:291px;border:1px solid #ddd}
.service-media{height:196px}
.service-body{height:94px;color:var(--white);text-align:center;padding-top:14px}
.service-body h3{font-family:"Montserrat",Arial,sans-serif;font-weight:500;font-size:18px;margin-bottom:5px}
.service-body p{font-size:11px;line-height:18px;padding:0 22px}
.service--red .service-body{background:var(--red)}
.service--navy .service-body{background:var(--navy)}

/* products */
.products-band{left:0;top:1259px;width:1200px;height:386px;background:var(--band)}
.section-title{left:0;width:1200px;text-align:center;font-family:"Montserrat",Arial,sans-serif;font-weight:400;font-size:28px;color:var(--ink)}
.product{top:1346px;width:216px;height:250px;background:var(--white);border:1px solid #d8d8d8;text-align:center}
.product-media{margin:22px auto 0;width:170px;height:150px;background:linear-gradient(180deg,#eef0f2,#d5d8dc)}
.product h4{margin-top:18px;font-family:"Montserrat",Arial,sans-serif;font-weight:400;font-size:17px;color:var(--red)}
.product p{margin-top:3px;font-size:12px;color:var(--light)}

/* faq */
.faq{left:243px;top:1760px;width:747px}
.faq-item{border:1px solid var(--line);margin-bottom:3px}
.faq-q{height:43px;display:flex;align-items:center;padding:0 16px;font-size:15px;color:#333}
.faq-q b{font-weight:400;width:36px;font-size:16px}
.faq-q span{flex:1}
.faq-item.is-open .faq-q{background:var(--red);color:var(--white)}
.faq-a{display:flex;padding:14px 24px 14px 20px;height:110px}
.faq-a b{font-weight:400;color:var(--red);width:42px;font-size:16px}
.faq-a p{flex:1;font-size:10px;line-height:17px;color:var(--muted)}

/* footer */
.site-footer{left:0;top:2118px;width:1200px;height:344px;background:var(--navy);color:#e2e0ef}
.f-col{top:49px}
.f-col h5{font-family:"Montserrat",Arial,sans-serif;font-weight:600;font-size:16px;color:var(--white);padding-bottom:8px;border-bottom:1px solid #6d679a;margin-bottom:12px}
.f-col li{list-style:none;font-size:13px;line-height:29px;white-space:nowrap}
.f-col--contact h5{width:152px}
.socials{display:flex;gap:4px;margin-top:4px}
.socials span{width:29px;height:29px;border-radius:50%;border:1.5px solid var(--white)}
.f-rule{left:145px;top:281px;width:910px;height:1px;background:#5b5590}
.f-copy{left:145px;top:298px;font-size:12px;color:#bdb9d8}
.f-legal{left:888px;top:297px;font-size:12px;color:#bdb9d8}
</style>
</head>
<body>

<header class="site-header abs">
  <a class="brand abs" href="#"><span class="brand-mark"></span><span>Northgate<br>Companies</span></a>
  <nav class="main-nav abs">
    <a href="#">About Us</a><a href="#">Packaging Products</a><a href="#">Packaging Equipment Specials</a><a href="#">Support</a><a href="#">Contact Us</a>
  </nav>
</header>

<section class="hero abs" role="img" aria-label="Photo of the company office building in winter with bare trees and snow"></section>
<div class="hero-rule abs"></div>
<h1 class="hero-title abs">LEADERS IN THE PACKAGING INDUSTRY</h1>
<h2 class="hero-sub abs">NORTHGATE PACKAGING EQUIPMENT</h2>
<a class="hero-btn abs" href="#">VIEW ALL</a>
<div class="slider-dots abs"><span class="is-active"></span><span></span><span></span><span></span></div>

<h2 class="intro-title abs">We are the packaging leader in the<br>Midwest for equipment sales and packaging supplies!</h2>
<p class="intro-text abs">Curabitur iaculis tempus eros Curabitur vel mi sit amet magna malesuada ultrices Ut nisi erat fermentum vel congue id euismod in elit Fusce ultricies orci ac feugiat suscipit leo massa sodales velit et scelerisque mi tortor at ipsum cligula augue bibendum accumsan vestibulum ut commodo a mi Morbi ornare gravida elit Integer congue augue et malesuada iaculis ipsum du</p>
<a class="btn-dark abs" href="#">READ MORE</a>

<article class="service service--red abs" style="left:153px">
  <div class="service-media" role="img" aria-label="Photo of a labeling machine" style="background:linear-gradient(180deg,#f4f4f4,#c9ccd0)"></div>
  <div class="service-body"><h3>Packaging Equipment</h3><p>ipsum dui aliquet felis at cursus magna nisl nec elit Praesent elementum elit</p></div>
</article>
<article class="service service--navy abs" style="left:453px">
  <div class="service-media" role="img" aria-label="Photo of a coil of strapping on a supply box" style="background:linear-gradient(180deg,#2a2a2a,#d9dbe0)"></div>
  <div class="service-body"><h3>Packaging Supplies</h3><p>ipsum dui aliquet felis at cursus magna nisl nec elit Praesent elementum elit</p></div>
</article>
<article class="service service--red abs" style="left:754px">
  <div class="service-media" role="img" aria-label="Photo of a pre-owned case sealer" style="background:linear-gradient(180deg,#efe9e2,#a8a097)"></div>
  <div class="service-body"><h3>Pre-Owned Equipment</h3><p>ipsum dui aliquet felis at cursus magna nisl nec elit Praesent elementum elit</p></div>
</article>

<section class="products-band abs"></section>
<h2 class="section-title abs" style="top:1290px">Our Products</h2>
<article class="product abs" style="left:144px"><div class="product-media" role="img" aria-label="Photo of a strapping machine"></div><h4>Equipment Tittle</h4><p>Aliquet felis at cursus magna nisl</p></article>
<article class="product abs" style="left:375px"><div class="product-media" role="img" aria-label="Photo of a label applicator on a stand"></div><h4>Equipment Tittle</h4><p>Aliquet felis at cursus magna nisl</p></article>
<article class="product abs" style="left:606px"><div class="product-media" role="img" aria-label="Photo of a robotic palletizing cell"></div><h4>Equipment Tittle</h4><p>Aliquet felis at cursus magna nisl</p></article>
<article class="product abs" style="left:837px"><div class="product-media" role="img" aria-label="Photo of a stretch wrapping machine"></div><h4>Equipment Tittle</h4><p>Aliquet felis at cursus magna nisl</p></article>

<h2 class="section-title abs" style="top:1702px">FAQ</h2>
<section class="faq abs">
  <div class="faq-item is-open">
    <div class="faq-q"><b>Q:</b><span>Nullam enim leo egestas id condimentum at laoreet?</span>
      <svg width="18" height="18" viewBox="0 0 18 18"><circle cx="9" cy="9" r="9" fill="#fff"/><rect x="4.5" y="7.8" width="9" height="2.4" fill="#a61e2f"/></svg></div>
    <div class="faq-a"><b>A:</b><p>You want a career that is interesting, safe, and makes money. To do that you need skills. But what skills? In what order? How much do you need to learn of each one before you can a job that pays more then promises? Our training method gets you directly into real web development where you have no training wheels to get used to. That means before we can even talk about learning to build Web Applications we need an editor to edit the "code".</p></div>
  </div>
  <div class="faq-item">
    <div class="faq-q"><b>Q:</b><span>Donec dictum lectus non odio Cras ?</span>
      <svg width="18" height="18" viewBox="0 0 18 18"><circle cx="9" cy="9" r="9" fill="#666"/><rect x="4.5" y="7.8" width="9" height="2.4" fill="#fff"/><rect x="7.8" y="4.5" width="2.4" height="9" fill="#fff"/></svg></div>
  </div>
  <div class="faq-item">
    <div class="faq-q"><b>Q:</b><span>Suspendisse quam leo molestie sed luctus quis feugiat in pede Fusce tellus ?</span>
      <svg width="18" height="18" viewBox="0 0 18 18"><circle cx="9" cy="9" r="9" fill="#666"/><rect x="4.5" y="7.8" width="9" height="2.4" fill="#fff"/><rect x="7.8" y="4.5" width="2.4" height="9" fill="#fff"/></svg></div>
  </div>
</section>

<footer class="site-footer abs">
  <div class="f-col abs" style="left:158px;width:150px"><h5>COMPANY</h5><ul><li>About Us</li><li>Careers</li><li>Privacy Policy</li><li>Our Team</li><li>Why Us</li></ul></div>
  <div class="f-col abs" style="left:348px;width:165px"><h5>PRODUCTS</h5><ul><li>Packaging Product</li><li>Packaging Equipments</li><li>Equipment Specials</li><li>Supplies</li></ul></div>
  <div class="f-col abs" style="left:552px;width:142px"><h5>RESOURCES</h5><ul><li>Support</li><li>FAQ</li><li>Tech Tips</li><li>Contact Us</li></ul></div>
  <div class="f-col f-col--contact abs" style="left:749px;width:240px"><h5>CONTACT US</h5><ul><li>2280 W Cedar Mill Rd, Lenexa, KS</li><li>(555) 214-3300</li><li>sales@northgateco.com</li><li>(555) 214-3390</li></ul>
    <div class="socials"><span></span><span></span><span></span><span></span></div></div>
  <div class="f-rule abs"></div>
  <p class="f-copy abs">© 2016 Company Name &nbsp;All right reserved</p>
  <p class="f-legal abs">Privacy Policy &nbsp;| &nbsp;Term of Use</p>
</footer>

</body>
</html>
```